Working Capital graphics

Our business advisory firm requires 9 images to be re-created and improved in the branding of our business.

The 9 images have been uploaded below and the colours and branding of the business can be found at the website www.tallowmereadvisory.com.au

```html
<!DOCTYPE html>
<html lang="en">
<head>
<meta charset="utf-8">
<title>Receivables Drivers</title>
<link href="https://fonts.googleapis.com/css2?family=Nunito+Sans:ital,wght@0,600;0,700;1,700;1,800&display=swap" rel="stylesheet">
<style>
  :root {
    --bg: #ffffff;
    --box: #55a7dc;
    --badge: #f0a042;
    --ink: #111111;
    --line: #111111;
    --badge-ink: #ffffff;
  }
  * { margin: 0; padding: 0; box-sizing: border-box; }
  html, body { width: 1200px; height: 1000px; overflow: hidden; background: var(--bg); }
  body { font-family: "Nunito Sans", Arial, sans-serif; color: var(--ink); }
  .canvas { position: relative; width: 1200px; height: 1000px; }
  .connectors { position: absolute; inset: 0; }
  .title {
    position: absolute; left: 55px; top: 150px;
    font-size: 35px; font-weight: 800; font-style: italic; letter-spacing: -0.3px;
  }
  .col-head {
    position: absolute; top: 168px; transform: translateX(-50%);
    font-size: 17px; font-weight: 700; white-space: nowrap;
  }
  .node {
    position: absolute; background: var(--box);
    display: flex; align-items: center; justify-content: center; text-align: center;
    font-style: italic; font-weight: 700; font-size: 16px; line-height: 1.15;
  }
  .node--root { left: 72px; top: 417px; width: 173px; height: 107px; }
  .node--process { left: 285px; width: 188px; height: 43px; }
  .node--driver { left: 540px; width: 265px; height: 31px; padding-left: 8px; }
  .node--sub { left: 867px; width: 282px; height: 29px; }
  .badge {
    position: absolute; left: 504px; width: 44px; height: 44px; border-radius: 50%;
    background: var(--badge); color: var(--badge-ink);
    display: flex; align-items: center; justify-content: center;
    font-size: 25px; font-weight: 800; font-style: italic;
  }
</style>
</head>
<body>
<div class="canvas">
  <svg class="connectors" width="1200" height="1000" viewBox="0 0 1200 1000" fill="none" stroke="var(--line)" stroke-width="2">
    <path d="M245 476H263M263 273V705M263 273H285M263 476H285M263 705H285"/>
    <path d="M473 273H495M495 222V322M495 222H505M495 272H505M495 322H505"/>
    <path d="M473 476H495M495 436V536M495 436H505M495 486H505M495 536H505"/>
    <path d="M473 705H495M495 674V776M495 674H505M495 725H505M495 776H505"/>
    <path d="M805 436H835M805 486H835M835 311V486M835 311H867M835 350H867M835 410H867M835 448H867"/>
    <path d="M805 536H835M835 498V575M835 498H867M835 536H867M835 575H867"/>
    <path d="M805 674H835M835 629V706M835 629H867M835 668H867M835 706H867"/>
    <path d="M805 725H835M835 725V834M835 757H867M835 795H867M835 834H867"/>
  </svg>

  <h1 class="title">Receivables</h1>
  <div class="col-head" style="left:374px">Sub-Process</div>
  <div class="col-head" style="left:667px">Drivers</div>
  <div class="col-head" style="left:1005px">Sub-Drivers</div>

  <div class="node node--root">Receivables<br>Drivers</div>

  <div class="node node--process" style="top:251px">Approval</div>
  <div class="node node--process" style="top:453px">Sales</div>
  <div class="node node--process" style="top:683px">Collections</div>

  <div class="node node--driver" style="top:207px">Differential terms</div>
  <div class="node node--driver" style="top:258px">Customer agreements</div>
  <div class="node node--driver" style="top:308px">Account set-up</div>
  <div class="node node--driver" style="top:421px">Receipt process</div>
  <div class="node node--driver" style="top:471px">Time to invoice</div>
  <div class="node node--driver" style="top:521px">Customer payment behaviour</div>
  <div class="node node--driver" style="top:659px">Payment cycle</div>
  <div class="node node--driver" style="top:710px">Collections</div>
  <div class="node node--driver" style="top:761px">Penalties</div>

  <div class="badge" style="top:200px">1</div>
  <div class="badge" style="top:250px">2</div>
  <div class="badge" style="top:300px">3</div>
  <div class="badge" style="top:414px">4</div>
  <div class="badge" style="top:464px">5</div>
  <div class="badge" style="top:514px">6</div>
  <div class="badge" style="top:652px">7</div>
  <div class="badge" style="top:703px">8</div>
  <div class="badge" style="top:754px">9</div>

  <div class="node node--sub" style="top:297px">Cash</div>
  <div class="node node--sub" style="top:336px">Banking process</div>
  <div class="node node--sub" style="top:396px">Sales delivery</div>
  <div class="node node--sub" style="top:434px">Invoicing</div>
  <div class="node node--sub" style="top:484px">KPI</div>
  <div class="node node--sub" style="top:522px">Relationship</div>
  <div class="node node--sub" style="top:561px">Pricing</div>
  <div class="node node--sub" style="top:615px">Closing date</div>
  <div class="node node--sub" style="top:654px">Time to process</div>
  <div class="node node--sub" style="top:692px">Invoicing cycle</div>
  <div class="node node--sub" style="top:742px">Tracking</div>
  <div class="node node--sub" style="top:780px">Methods</div>
  <div class="node node--sub" style="top:819px">Agencies</div>
</div>
</body>
</html>
```